A start-up named "Corvane Therapeutics" - needs a new PowerPoint design

We need a new PowerPoint Design for an early-stage start-up named "Corvane Therapeutics" seeking to disrupt the current approach towards drug discovery within aging disorders.

We would like to build on Corvane's legacy, the founder of the modern science of genetics, by employing a multidisciplinary approach, experimenting, and providing elderly patients the attention they deserve.

We have selected the suffix "therapeutics" intentionally as it stands for (a medicine) the treatment of disease; the science of healing. Alzheimer’s treatment is a huge, urgent, unmet need:
- Shift from a disease-management system to a preventive medicine system
- Focus on increasing the health span, not only the life span

Target Market(s)

Pharma/ Biotech Executives Medical Institutions Healthcare professionals (MDs, nurses, payors, pharmacists, etc.) Patients

Industry/Entity Type

Healthcare

Other font styles liked:
• Celias

Colors
0054AA
0677BA
7BADD7
CADEEF
E8F1F8
E54698
E96AAD
F1A4CE
F9D9EA
FCEFF6
A7469A
B969AE
D3A5CF
EDDBEB
F8F0F9
6B429C
8869AF
B7A5CE
E3DAEB
F3F0F8

Requirements
Must have
• - differentiate from other companies named after Corvane - differentiate from other Pharma/ Biotech companies
Nice to have
• simplicity/ minimalist logo vivid colors gradient 3D Life-Sciences inspired Simple geometry Balance
Should not have
• mascot/ emblem watermark logo animated ink style nature-inspired inventive typography artistic chaos

```html
<!DOCTYPE html>
<html lang="en">
<head>
<meta charset="utf-8">
<title>Corvane Therapeutics – Presentation Template</title>
<link rel="stylesheet" href="https://fonts.googleapis.com/css2?family=Inter:wght@400;500;600;700;800&display=swap">
<style>
  :root{
    --page:#f1f1f3;
    --white:#ffffff;
    --ink:#1f1f24;
    --muted:#3a3a40;
    --blue-deep:#0054AA;
    --blue:#0677BA;
    --blue-soft:#7BADD7;
    --pink:#E54698;
    --pink-soft:#E96AAD;
    --magenta:#C8307A;
    --plum:#A7469A;
    --violet:#6B429C;
    --violet-mid:#8869AF;
    --row-alt:#f3f3f5;
    --grid:#e2e2e6;
  }
  *{box-sizing:border-box;margin:0;padding:0}
  html,body{width:1200px;height:1200px;overflow:hidden;background:var(--page)}
  body{position:relative;font-family:"Inter",Arial,sans-serif;color:var(--ink)}

  .slide{position:absolute;width:466px;height:262px;background:var(--white);overflow:hidden}
  .col-a{left:122px}.col-b{left:607px}
  .row-1{top:43px}.row-2{top:328px}.row-3{top:614px}.row-4{top:899px}

  .slide-title{position:absolute;left:15px;top:17px;font-size:15px;font-weight:600;letter-spacing:.1px;color:var(--ink)}
  .brand{position:absolute;right:14px;top:19px;display:flex;align-items:center;gap:4px}
  .brand-mark{width:11px;height:11px;background:var(--violet)}
  .brand-name{font-size:11px;font-weight:600;color:var(--blue)}

  .footer-band{position:absolute;right:0;bottom:7px;width:131px;height:18px;
    background:linear-gradient(90deg,var(--magenta),var(--violet-mid));
    clip-path:polygon(12px 0,100% 0,100% 100%,0 100%)}
  .footer-band span{position:absolute;right:15px;top:5px;font-size:4.6px;color:var(--white)}
  .page-no{position:absolute;left:15px;bottom:12px;font-size:5px;font-weight:700;color:var(--blue-deep)}

  /* cover */
  .cover-art{position:absolute;inset:0}
  .cover-brand{position:absolute;left:0;right:0;top:46px;display:flex;justify-content:center;align-items:center;gap:6px}
  .cover-brand .brand-mark{width:16px;height:16px;background:var(--white)}
  .cover-brand .brand-name{font-size:18px;font-weight:500;color:var(--white)}
  .cover-title{position:absolute;left:0;right:0;top:92px;text-align:center;font-size:23px;font-weight:700;color:var(--white)}
  .cover-lede{position:absolute;left:70px;right:70px;top:129px;text-align:center;font-size:6.6px;line-height:9.2px;color:var(--white)}
  .cover-copy{position:absolute;left:15px;top:250px;font-size:4.6px;color:var(--muted)}

  /* template style */
  .bullets{position:absolute;left:15px;right:14px;top:57px;list-style:none}
  .bullets li{position:relative;padding-left:7px;font-size:8.9px;line-height:11.6px;color:var(--ink)}
  .bullets li::before{content:"•";position:absolute;left:0;color:var(--pink)}
  .bullets li.sub{margin-top:5px;padding-left:14px;font-size:7.8px;line-height:10.4px}
  .bullets li.sub::before{content:"–";left:6px}

  /* about */
  .banner{position:absolute;left:0;top:48px;width:466px;height:104px;
    background:linear-gradient(90deg,#e9c3d6 0%,#cfd3ea 40%,#bfd2ee 70%,#9fb4de 100%)}
  .section-head{font-size:9.6px;font-weight:700;color:var(--blue-deep)}
  .about-body{position:absolute;left:20px;right:20px;top:165px;text-align:center}
  .about-body p{margin-top:3px;font-size:6.9px;line-height:9.2px;color:var(--ink)}

  /* team */
  .member{position:absolute;top:52px;width:134px;text-align:center}
  .member .photo{height:134px;border-bottom:3px solid var(--plum);
    background:linear-gradient(180deg,#b9c4c9,#8d9aa3)}
  .member:nth-child(odd) .photo{background:linear-gradient(180deg,#9fb87a,#d8d2c4)}
  .member .name{margin-top:9px;font-size:8.4px;font-weight:600;color:var(--blue-deep)}
  .member .role{margin-top:2px;font-size:6.8px;color:var(--ink)}

  /* mission */
  .mission-text{position:absolute;left:15px;top:71px;width:160px}
  .mission-text p{margin-top:2px;font-size:6.9px;line-height:9.3px;color:var(--ink)}
  .mission-text p + p{margin-top:9px}
  .divider{position:absolute;left:197px;top:54px;width:1px;height:177px;background:var(--grid)}
  .chart{position:absolute;left:0;top:0}
  .chart text{font-family:"Inter",Arial,sans-serif}

  /* services */
  .card{position:absolute;top:55px;width:104px;height:137px;text-align:center;color:var(--white)}
  .card.purple{background:linear-gradient(180deg,#7a45a0 0%,#b25aa8 55%,#e56fb0 100%)}
  .card.blue{background:linear-gradient(180deg,#0677BA 0%,#1157a9 100%)}
  .card svg{margin-top:19px}
  .card h3{margin-top:9px;font-size:9.5px;font-weight:600}
  .card p{margin:3px 8px 0;font-size:6.1px;line-height:8.2px}
  .services-note{position:absolute;left:18px;right:18px;top:202px;text-align:center;font-size:6.9px;line-height:9.3px;color:var(--ink)}

  /* table */
  .data-table{position:absolute;left:15px;top:56px;width:436px;border-collapse:collapse;border-bottom:1px solid var(--pink)}
  .data-table th{height:27px;background:var(--pink);color:var(--white);font-size:8.2px;font-weight:600;text-align:left;padding-left:4px}
  .data-table td{height:27.4px;font-size:8.2px;padding-left:4px;color:var(--ink)}
  .data-table td:first-child{color:var(--blue-deep);font-weight:600}
  .data-table tr:nth-child(even) td{background:var(--row-alt)}

  /* closing */
  .closing-brand{position:absolute;left:0;right:0;top:104px;display:flex;justify-content:center;align-items:center;gap:14px}
  .closing-brand .brand-mark{width:44px;height:44px;background:var(--violet)}
  .closing-brand .brand-name{font-size:30px;font-weight:600;line-height:30px;color:var(--blue)}
  .closing-brand .brand-name small{display:block;font-size:17px;line-height:22px}
</style>
</head>
<body>

<!-- 1 Cover -->
<section class="slide col-a row-1">
  <svg class="cover-art" width="466" height="262" viewBox="0 0 466 262" role="img" aria-label="Laboratory photo with DNA strands under a purple-pink overlay">
    <defs>
      <linearGradient id="coverGrad" x1="0" y1="1" x2="1" y2="0">
        <stop offset="0" stop-color="#7a3fa2"/>
        <stop offset=".55" stop-color="#b04f9e"/>
        <stop offset="1" stop-color="#de6496"/>
      </linearGradient>
    </defs>
    <polygon points="0,0 466,0 466,172 0,233" fill="url(#coverGrad)"/>
    <polygon points="247,208 466,179 466,240" fill="var(--blue)"/>
  </svg>
  <div class="cover-brand"><span class="brand-mark"></span><span class="brand-name">Corvane</span></div>
  <h1 class="cover-title">Presentation Title Goes Here</h1>
  <p class="cover-lede">Lorem ipsum dolor sit amet, consectetur adipiscing elit. Curabitur at fringilla velit. Nulla en quis erat et ligula aliquam sagittis in viverra mauris. Pellentesque pharetra.</p>
  <p class="cover-copy">Copywrite Statement 2022</p>
</section>

<!-- 2 Template Style -->
<section class="slide col-b row-1">
  <h2 class="slide-title">Template Style</h2>
  <div class="brand"><span class="brand-mark"></span><span class="brand-name">Corvane</span></div>
  <ul class="bullets">
    <li>Lorem ipsum dolor sit amet, consectetur adipiscing elit. Curabitur at fringilla velit. In ac sagittis nulla. Nulla quis erat et ligula aliquam sagittis in viverra mauris. Pellentesque pharetra hendrerit orci at.</li>
    <li class="sub">Donec vel suscipit purus, ultrices ornare neque. Sed nec est a lacus lacinia venenatis non at est. Vestibulum vitae lorem lectus. Phasellus gravida mauris a sapien elementum malesuada. Vestibulum ut urna eu dolor suscipit condimentum. Curabitur sed commodo leo. Phasellus faucibus sem ante.</li>
  </ul>
  <p class="page-no">2</p>
  <div class="footer-band"><span>Copywrite Statement 2022</span></div>
</section>

<!-- 3 About Us -->
<section class="slide col-a row-2">
  <h2 class="slide-title">About Us</h2>
  <div class="brand"><span class="brand-mark"></span><span class="brand-name">Corvane</span></div>
  <div class="banner" role="img" aria-label="Laboratory glassware and DNA helix photo banner"></div>
  <div class="about-body">
    <h3 class="section-head">Section Header</h3>
    <p>Lorem ipsum dolor sit amet, consectetur adipiscing elit. Curabitur at fringilla velit. In ac sagittis nulla. Nulla quis erat et ligula aliquam sagittis in viverra mauris. Pellentesque pharetra hendrerit orci at. Phasellus gravida mauris a sapien elementum malesuada. Vestibulum ut urna eu dolor suscipit condimentum. Curabitur sed commodo leo.</p>
  </div>
  <p class="page-no">3</p>
  <div class="footer-band"><span>Copywrite Statement 2022</span></div>
</section>

<!-- 4 Meet Our Team -->
<section class="slide col-b row-2">
  <h2 class="slide-title">Meet Our Team</h2>
  <div class="brand"><span class="brand-mark"></span><span class="brand-name">Corvane</span></div>
  <div class="team">
    <div class="member" style="left:15px"><div class="photo" role="img" aria-label="Portrait photo of a team member"></div><p class="name">Enter Name Here</p><p class="role">Subtitle</p></div>
    <div class="member" style="left:166px"><div class="photo" role="img" aria-label="Portrait photo of a team member"></div><p class="name">Enter Name Here</p><p class="role">Subtitle</p></div>
    <div class="member" style="left:318px"><div class="photo" role="img" aria-label="Portrait photo of a team member"></div><p class="name">Enter Name Here</p><p class="role">Subtitle</p></div>
  </div>
  <p class="page-no">4</p>
  <div class="footer-band"><span>Copywrite Statement 2022</span></div>
</section>

<!-- 5 Our Mission -->
<section class="slide col-a row-3">
  <h2 class="slide-title">Our Mission</h2>
  <div class="brand"><span class="brand-mark"></span><span class="brand-name">Corvane</span></div>
  <div class="mission-text">
    <h3 class="section-head">Section Header</h3>
    <p>Donec vel suscipit purus, ultrices ornare neque. Sed nec est a lacus lacinia venenatis non at est. Vestibulum vitae lorem lectus. Phasellus gravida mauris a sapien elementum malesuada. Vestibulum ut urna eu dolor.</p>
    <p>Lorem ipsum dolor sit amet, consectetur adipiscing elit. Curabitur at fringilla velit. In ac sagittis nulla. Nulla quis erat et ligula aliquam sagittis in viverra mauris. Pellentesque pharetra hendrerit orci at.</p>
  </div>
  <div class="divider"></div>
  <svg class="chart" width="466" height="262" viewBox="0 0 466 262">
    <defs>
      <linearGradient id="areaGrad" x1="0" y1="0" x2="0" y2="1">
        <stop offset="0" stop-color="#8a45a0"/>
        <stop offset="1" stop-color="#e56aae"/>
      </linearGradient>
    </defs>
    <text x="334" y="68" text-anchor="middle" font-size="7.4" font-weight="600" fill="#0054AA">Chart Title</text>
    <g stroke="#e2e2e6" stroke-width=".6">
      <line x1="237" x2="432" y1="75" y2="75"/><line x1="237" x2="432" y1="87.9" y2="87.9"/>
      <line x1="237" x2="432" y1="100.8" y2="100.8"/><line x1="237" x2="432" y1="113.7" y2="113.7"/>
      <line x1="237" x2="432" y1="126.6" y2="126.6"/><line x1="237" x2="432" y1="139.5" y2="139.5"/>
      <line x1="237" x2="432" y1="152.4" y2="152.4"/><line x1="237" x2="432" y1="165.3" y2="165.3"/>
      <line x1="237" x2="432" y1="178.2" y2="178.2"/><line x1="237" x2="432" y1="191.1" y2="191.1"/>
      <line x1="237" x2="432" y1="204" y2="204"/>
    </g>
    <g font-size="6.4" fill="#3a3a40" text-anchor="end">
      <text x="231" y="77">10</text><text x="231" y="90">9</text><text x="231" y="103">8</text>
      <text x="231" y="116">7</text><text x="231" y="129">6</text><text x="231" y="142">5</text>
      <text x="231" y="155">4</text><text x="231" y="168">3</text><text x="231" y="180">2</text>
      <text x="231" y="193">1</text><text x="231" y="206">0</text>
    </g>
    <polygon points="237,148.5 302,100.8 368,158.9 432,152.4 432,204 237,204" fill="var(--blue)"/>
    <polygon points="237,173 302,126.6 368,180.8 432,100.8 432,204 237,204" fill="url(#areaGrad)"/>
    <g font-size="6.4" fill="#3a3a40" text-anchor="middle">
      <text x="237" y="217">Category 1</text><text x="302" y="217">Category 2</text>
      <text x="368" y="217">Category 3</text><text x="432" y="217">Category 4</text>
    </g>
  </svg>
  <p class="page-no">5</p>
  <div class="footer-band"><span>Copywrite Statement 2022</span></div>
</section>

<!-- 6 Medical Services -->
<section class="slide col-b row-3">
  <h2 class="slide-title">Medical Services</h2>
  <div class="brand"><span class="brand-mark"></span><span class="brand-name">Corvane</span></div>

  <div class="card purple" style="left:15px">
    <svg width="24" height="32" viewBox="0 0 24 32" fill="none" stroke="#fff" stroke-width="1.3"><rect x="4" y="2" width="17" height="28" rx="1.5"/><circle cx="14" cy="10" r="3.5"/><path d="M14 8v4M12 10h4M8 17h10M8 21h10M8 25h10M2 7h4M2 13h4M2 19h4"/></svg>
    <h3>Section Header</h3>
    <p>Lorem ipsum dolor sit amet, consecteturat es adipiscing elit. Curabitur fringilla velit. In ac sagittis nulla. Nulla quis erat et.</p>
  </div>
  <div class="card blue" style="left:124px">
    <svg width="32" height="32" viewBox="0 0 32 32" fill="none" stroke="#fff" stroke-width="1.5"><rect x="4" y="10" width="6" height="19" rx="3"/><path d="M4 20h6"/><path d="M18 4h8M20 4v10l-6 13a2 2 0 0 0 2 3h12a2 2 0 0 0 2-3l-6-13V4"/><path d="M16 23h14" /></svg>
    <h3>Section Header</h3>
    <p>Lorem ipsum dolor sit amet, consecteturat es adipiscing elit. Curabitur fringilla velit. In ac sagittis nulla. Nulla quis erat et.</p>
  </div>
  <div class="card purple" style="left:233px">
    <svg width="32" height="32" viewBox="0 0 32 32" fill="none" stroke="#fff" stroke-width="1.5"><circle cx="16" cy="16" r="9"/><path d="M16 2v5M16 25v5M2 16h5M25 16h5M6 6l3.5 3.5M22.5 22.5L26 26M26 6l-3.5 3.5M9.5 22.5L6 26"/><circle cx="13" cy="14" r="2" fill="#fff"/><circle cx="19" cy="18" r="1.6" fill="#fff"/></svg>
    <h3>Section Header</h3>
    <p>Lorem ipsum dolor sit amet, consecteturat es adipiscing elit. Curabitur fringilla velit. In ac sagittis nulla. Nulla quis erat et.</p>
  </div>
  <div class="card blue" style="left:342px">
    <svg width="32" height="32" viewBox="0 0 32 32"><g transform="rotate(45 16 16)" fill="#fff"><rect x="11" y="2" width="10" height="13" rx="5"/><rect x="11.8" y="16.5" width="8.4" height="12" rx="4.2" fill="none" stroke="#fff" stroke-width="1.6"/></g></svg>
    <h3>Section Header</h3>
    <p>Lorem ipsum dolor sit amet, consecteturat es adipiscing elit. Curabitur fringilla velit. In ac sagittis nulla. Nulla quis erat et.</p>
  </div>

  <p class="services-note">Lorem ipsum dolor sit amet, consectetur adipiscing elit. Curabitur at fringilla velit. In ac sagittis nulla. Nulla quis erat et ligula aliquam sagittis in viverra mauris. Pellentesque pharetra hendrerit orci at. Phasellus gravida mauris.</p>
  <p class="page-no">6</p>
  <div class="footer-band"><span>Copywrite Statement 2022</span></div>
</section>

<!-- 7 Table -->
<section class="slide col-a row-4">
  <h2 class="slide-title">Table Slide</h2>
  <div class="brand"><span class="brand-mark"></span><span class="brand-name">Corvane</span></div>
  <table class="data-table">
    <thead><tr><th>Data</th><th>Header</th><th>Header</th><th>Header</th><th>Header</th><th>Header</th><th>Header</th><th>Header</th></tr></thead>
    <tbody>
      <tr><td>Value</td><td>00</td><td>00</td><td>00</td><td>00</td><td>00</td><td>00</td><td>00</td></tr>
      <tr><td>Value</td><td>00</td><td>00</td><td>00</td><td>00</td><td>00</td><td>00</td><td>00</td></tr>
      <tr><td>Value</td><td>00</td><td>00</td><td>00</td><td>00</td><td>00</td><td>00</td><td>00</td></tr>
      <tr><td>Value</td><td>00</td><td>00</td><td>00</td><td>00</td><td>00</td><td>00</td><td>00</td></tr>
      <tr><td>Value</td><td>00</td><td>00</td><td>00</td><td>00</td><td>00</td><td>00</td><td>00</td></tr>
    </tbody>
  </table>
  <p class="page-no">7</p>
  <div class="footer-band"><span>Copywrite Statement 2022</span></div>
</section>

<!-- 8 Closing -->
<section class="slide col-b row-4">
  <div class="closing-brand"><span class="brand-mark"></span><span class="brand-name">Corvane<small>Therapeutics</small></span></div>
</section>

</body>
</html>
```